Tolvik Commercial Cleaning is lookong for a new business card design.

A fresh new design that's professional and stylish. We need a serious upgrade to our business cards. I have included pictures of our existing ones. Our clients include professional individuals and business owners. We woupdblike something professional and upbeat. Please have fun and see what you come uo with.

Target Market(s)

Property managers, business owners, facility managers and other similar professionals

Industry/Entity Type

Janitorial

Contact Information for Business Card

Name, cell, office number, email, web address

Font styles to use
Sans Serif

Colors

Designer to choose colors to be used in the design.

Requirements
Must have
• please use the green color in our logo
Nice to have
• Bar code
Should not have
• Address

```html
<!DOCTYPE html>
<html lang="en">
<head>
<meta charset="utf-8">
<title>Tolvik Commercial Cleaning – Business Card</title>
<link href="https://fonts.googleapis.com/css2?family=Open+Sans:wght@400;600;700&family=Quicksand:wght@700&display=swap" rel="stylesheet">
<style>
  :root {
    --backdrop: #1b1b1e;
    --front-blue: #4477ae;
    --brand-navy: #0d5a9a;
    --card-dark: #222226;
    --brand-green: #38b659;
    --brand-blue: #3f6fb0;
    --text-light: #ffffff;
  }
  * { margin: 0; padding: 0; box-sizing: border-box; }
  html, body {
    width: 1200px; height: 780px; overflow: hidden;
    background: var(--backdrop);
  }
  .canvas {
    position: relative; width: 1200px; height: 780px;
    display: flex; align-items: center; justify-content: center; gap: 40px;
  }
  .card {
    position: relative; width: 540px; height: 310px;
    border-radius: 20px; overflow: hidden;
  }
  /* Front side */
  .card--front {
    background: var(--front-blue);
    display: flex; flex-direction: column; align-items: center; justify-content: center;
  }
  .brand-name {
    font-family: "Quicksand", sans-serif; font-weight: 700;
    color: var(--brand-navy); line-height: 1;
  }
  .card--front .brand-name--main { font-size: 96px; letter-spacing: 1px; }
  .card--front .brand-name--sub { font-size: 26px; margin-top: 10px; letter-spacing: 1px; }

  /* Back side */
  .card--back { background: var(--card-dark); }
  .wave { position: absolute; inset: 0; width: 100%; height: 100%; }
  .back-brand {
    position: absolute; left: 34px; top: 96px; width: 230px;
    display: flex; flex-direction: column; align-items: flex-start;
  }
  .card--back .brand-name { color: var(--brand-green); }
  .card--back .brand-name--main { font-size: 62px; }
  .card--back .brand-name--sub { font-size: 15px; margin-top: 8px; }
  .divider {
    position: absolute; left: 276px; top: 34px;
    width: 1px; height: 150px; background: var(--text-light);
  }
  .contact {
    position: absolute; left: 298px; top: 34px;
    font-family: "Open Sans", sans-serif; color: var(--text-light);
  }
  .contact__name { font-size: 24px; font-weight: 700; line-height: 1.1; }
  .contact__first { color: var(--brand-green); }
  .contact__last { color: var(--brand-blue); }
  .contact__title { font-size: 13px; font-weight: 600; margin-top: 2px; }
  .contact__list { list-style: none; margin-top: 14px; }
  .contact__item {
    display: flex; align-items: center; gap: 8px;
    font-size: 12.5px; line-height: 1.65;
  }
  .contact__icon { width: 13px; height: 13px; flex: none; }
</style>
</head>
<body>
<main class="canvas">

  <section class="card card--front" aria-label="Business card front">
    <div class="brand-name brand-name--main">Tolvik</div>
    <div class="brand-name brand-name--sub">Commercial Cleaning</div>
  </section>

  <section class="card card--back" aria-label="Business card back">
    <svg class="wave" viewBox="0 0 540 310" aria-hidden="true">
      <path d="M40,310 C200,292 330,262 410,216 C458,190 495,184 540,182 L540,310 Z" fill="var(--brand-green)"/>
      <path d="M50,296 C210,274 330,246 402,204 C452,176 492,170 530,168" fill="none" stroke="var(--brand-blue)" stroke-width="4" stroke-linecap="round"/>
    </svg>

    <div class="back-brand">
      <div class="brand-name brand-name--main">Tolvik</div>
      <div class="brand-name brand-name--sub">Commercial Cleaning</div>
    </div>

    <div class="divider"></div>

    <div class="contact">
      <div class="contact__name"><span class="contact__first">Maren</span> <span class="contact__last">Ostby</span></div>
      <div class="contact__title">Director</div>
      <ul class="contact__list">
        <li class="contact__item">
          <svg class="contact__icon" viewBox="0 0 16 16" aria-hidden="true"><path d="M3.5 1.5l2.5 0 1 3.5-1.8 1.2a8 8 0 0 0 4.6 4.6l1.2-1.8 3.5 1v2.5c0 .8-.7 1.5-1.5 1.5A12 12 0 0 1 2 3c0-.8.7-1.5 1.5-1.5z" fill="var(--brand-green)"/></svg>
          (555) 014-2270
        </li>
        <li class="contact__item">
          <svg class="contact__icon" viewBox="0 0 16 16" aria-hidden="true"><rect x="1" y="3" width="14" height="10" rx="1.5" fill="var(--brand-green)"/><path d="M1.5 4l6.5 5 6.5-5" fill="none" stroke="var(--card-dark)" stroke-width="1.4"/></svg>
          maren@tolvikcleaning.com
        </li>
        <li class="contact__item">
          <svg class="contact__icon" viewBox="0 0 16 16" aria-hidden="true"><circle cx="8" cy="8" r="7" fill="var(--brand-green)"/><path d="M1 8h14M8 1c-3 3.5-3 10.5 0 14M8 1c3 3.5 3 10.5 0 14" fill="none" stroke="var(--card-dark)" stroke-width="1"/></svg>
          www.tolvikcleaning.com
        </li>
      </ul>
    </div>
  </section>

</main>
</body>
</html>
```